Modern Business Card

Modern professional business card with more than just logo and demographic info. Something memorable.

We are a trendy/modern chiropractic group with an emphasis on neurology, hence the minimalist-type brain logo. We want to convey that modern and technical aspect with professionalism and the elite nature of our practice environment.

```html
<!DOCTYPE html>
<html lang="en">
<head>
<meta charset="utf-8">
<title>Clarion Spine – Business Card</title>
<link rel="stylesheet" href="https://fonts.googleapis.com/css2?family=Khand:wght@600&family=Quattrocento:wght@400;700&display=swap">
<style>
  :root {
    --page: #ebe8e5;
    --panel-blue: #4f6fa8;
    --panel-blue-deep: #3f5c94;
    --frost: #e4ddd8;
    --frost-light: #efeae6;
    --divider: #4a3b3a;
    --ink-light: #f3f4f8;
    --ink-soft: #dde3ef;
    --ink-address: #e6c9c6;
    --ink-dark: #2b2324;
    --mark-blue: #3f5f99;
  }
  * { margin: 0; padding: 0; box-sizing: border-box; }
  html, body { width: 1200px; height: 1054px; overflow: hidden; }
  body { background: var(--page); position: relative; }

  .card {
    position: absolute;
    left: 100px; top: 225px;
    width: 1000px; height: 604px;
    overflow: hidden;
    box-shadow: 0 10px 30px rgba(0,0,0,.18);
  }
  .card-shapes { position: absolute; inset: 0; }

  .identity { position: absolute; left: 50px; top: 58px; }
  .person-name {
    font-family: "Khand", sans-serif; font-weight: 600;
    font-size: 40px; line-height: 1; color: var(--ink-light);
  }
  .person-role {
    font-family: "Quattrocento", serif; font-size: 24px;
    color: var(--ink-soft); margin-top: 10px;
  }

  .contacts { position: absolute; left: 50px; top: 348px; list-style: none; }
  .contact {
    display: flex; align-items: center; height: 37.5px;
    font-family: "Quattrocento", serif; font-size: 24px; color: var(--ink-soft);
  }
  .contact svg { width: 22px; height: 22px; margin-right: 21px; fill: var(--ink-soft); }
  .address {
    position: absolute; left: 50px; top: 468px;
    font-family: "Quattrocento", serif; font-size: 24px; line-height: 37px;
    color: var(--ink-address); font-style: normal;
  }

  .brand {
    position: absolute; left: 560px; top: 150px; width: 400px;
    display: flex; flex-direction: column; align-items: center;
  }
  .brand-dot {
    width: 110px; height: 110px; border-radius: 50%;
    background: var(--mark-blue); margin-bottom: 40px;
  }
  .brand-name {
    font-family: "Quattrocento", serif; font-weight: 700;
    font-size: 58px; line-height: 1; letter-spacing: 2px;
    color: var(--ink-dark); text-transform: uppercase; text-align: center;
  }
</style>
</head>
<body>
  <article class="card">
    <svg class="card-shapes" viewBox="0 0 1000 604" width="1000" height="604" aria-hidden="true">
      <defs>
        <linearGradient id="frostFill" x1="0" y1="0" x2="1" y2="1">
          <stop offset="0" stop-color="var(--frost-light)"/>
          <stop offset="1" stop-color="var(--frost)"/>
        </linearGradient>
        <linearGradient id="blueFill" x1="0" y1="0" x2="0" y2="1">
          <stop offset="0" stop-color="var(--panel-blue)"/>
          <stop offset="1" stop-color="var(--panel-blue-deep)"/>
        </linearGradient>
      </defs>
      <rect class="frost-panel" width="1000" height="604" fill="url(#frostFill)"/>
      <path class="curve-edge" d="M0 0 H586 Q470 300 566 604 H0 Z" fill="var(--divider)"/>
      <path class="blue-panel" d="M0 0 H577 Q462 300 555 604 H0 Z" fill="url(#blueFill)"/>
    </svg>

    <header class="identity">
      <h1 class="person-name">Daniel Reyes Hart</h1>
      <p class="person-role">Managing Director</p>
    </header>

    <ul class="contacts">
      <li class="contact">
        <svg viewBox="0 0 24 24" aria-hidden="true"><path d="M2 8c0-3 4-4 10-4s10 1 10 4v2h-5V8H7v2H2zM6 11h12l3 8H3z"/></svg>
        555-240-1180
      </li>
      <li class="contact">
        <svg viewBox="0 0 24 24" aria-hidden="true"><path d="M2 5h20v14H2zm2 2v.5l8 6 8-6V7zm0 3v7h16v-7l-8 6z"/></svg>
        daniel@clarionspine.com
      </li>
      <li class="contact">
        <svg viewBox="0 0 24 24" aria-hidden="true"><path d="M12 2a10 10 0 1 0 0 20 10 10 0 0 0 0-20zm-1 2.1V8H7.6A8 8 0 0 1 11 4.1zm2 0A8 8 0 0 1 16.4 8H13zM4.3 10H11v4H4.3a8 8 0 0 1 0-4zM13 10h6.7a8 8 0 0 1 0 4H13zm-5.4 6H11v3.9A8 8 0 0 1 7.6 16zm5.4 0h3.4a8 8 0 0 1-3.4 3.9z"/></svg>
        www.clarionspine.com
      </li>
    </ul>

    <address class="address">418 Harbor Lane, Fairview,<br>Westbrook, US 204816</address>

    <div class="brand">
      <span class="brand-dot" aria-hidden="true"></span>
      <p class="brand-name">Clarion<br>Spine</p>
    </div>
  </article>
</body>
</html>
```